Automotive Accessories Business Card

Design a business template that match our new logo design and our industry.

https://www.qelmotorgear.com/

Target Market(s)

Aftermarket auto parts and accessories

Industry/Entity Type

automotive

Contact Information for Business Card

company logo

Font styles to use
Serif
Sans Serif

Colors
EB3D1F
EC4F4E
F09395
F8D3D4
FCEDEE

```html
<!DOCTYPE html>
<html lang="en">
<head>
<meta charset="utf-8">
<title>QEL Motor Gear – Business Card</title>
<link href="https://fonts.googleapis.com/css2?family=Montserrat:wght@400;700&display=swap" rel="stylesheet">
<style>
  :root {
    --stage: #9a9a9a;
    --paper: #ffffff;
    --ink: #3f3d3f;
    --red: #d91f26;
    --charcoal: #444244;
    --charcoal-mark: #383638;
  }
  * { margin: 0; padding: 0; box-sizing: border-box; }
  html, body { width: 1200px; height: 1059px; overflow: hidden; }
  body {
    background: var(--stage);
    font-family: "Montserrat", Arial, sans-serif;
    color: var(--ink);
    position: relative;
  }
  .card {
    position: absolute;
    width: 690px;
    height: 392px;
    border-radius: 20px;
    overflow: hidden;
  }
  .card--front { left: 256px; top: 89px; background: var(--paper); }
  .card--back { left: 254px; top: 569px; background: var(--charcoal); }

  .brand {
    position: absolute;
    left: 44px;
    top: 176px;
    width: 270px;
    display: flex;
    align-items: center;
    gap: 10px;
    white-space: nowrap;
  }
  .brand__square { width: 22px; height: 22px; background: var(--red); flex: none; }
  .brand__name {
    font-weight: 700;
    font-size: 23px;
    letter-spacing: 0.3px;
    color: var(--ink);
  }

  .divider {
    position: absolute;
    left: 344px;
    top: 102px;
    width: 1px;
    height: 186px;
    background: var(--red);
  }
  .contact { position: absolute; left: 373px; top: 98px; white-space: nowrap; }
  .contact__name {
    font-weight: 700;
    font-size: 25px;
    letter-spacing: 1px;
    color: var(--red);
    line-height: 1.1;
  }
  .contact__role { font-size: 16.5px; margin-top: 2px; }
  .contact__address { font-size: 16.5px; line-height: 21px; margin-top: 14px; }
  .contact__list { list-style: none; margin-top: 12px; }
  .contact__item {
    display: flex;
    align-items: center;
    gap: 6px;
    font-size: 16.5px;
    height: 27px;
  }
  .contact__item svg { width: 12px; height: 12px; flex: none; }

  .band {
    position: absolute;
    left: 0; bottom: 0;
    width: 100%;
    height: 12px;
  }

  .back-mark {
    position: absolute;
    inset: 0;
    display: flex;
    align-items: center;
    justify-content: center;
    gap: 14px;
    white-space: nowrap;
  }
  .back-mark__square { width: 36px; height: 36px; background: var(--charcoal-mark); flex: none; }
  .back-mark__name {
    font-weight: 700;
    font-size: 38px;
    letter-spacing: 0.5px;
    color: var(--charcoal-mark);
  }
</style>
</head>
<body>
  <section class="card card--front" aria-label="Business card front">
    <div class="brand">
      <span class="brand__square"></span>
      <span class="brand__name">QEL MOTOR GEAR</span>
    </div>
    <div class="divider"></div>
    <div class="contact">
      <h1 class="contact__name">DANA WHITFIELD</h1>
      <p class="contact__role">CEO/Founder</p>
      <p class="contact__address">240 W. Cedar Ave. Unit B<br>Riverside, CA, 92501</p>
      <ul class="contact__list">
        <li class="contact__item">
          <svg viewBox="0 0 12 12" aria-hidden="true"><path fill="#d91f26" d="M2.5 1l2 2.2-1 1.2c.6 1.4 1.7 2.5 3.1 3.1l1.2-1 2.2 2-1 1.5C5.3 10.2 1.8 6.7 1 2z"/></svg>
          1-866-555-0142
        </li>
        <li class="contact__item">
          <svg viewBox="0 0 12 12" aria-hidden="true"><rect x="0.5" y="2" width="11" height="8" fill="#d91f26"/><path d="M1 2.5l5 4 5-4" stroke="#fff" stroke-width="1" fill="none"/></svg>
          sales@qelmotorgear.com
        </li>
        <li class="contact__item">
          <svg viewBox="0 0 12 12" aria-hidden="true"><g fill="none" stroke="#d91f26" stroke-width="1"><circle cx="6" cy="6" r="5"/><ellipse cx="6" cy="6" rx="2.2" ry="5"/><path d="M1 6h10M2 3.5h8M2 8.5h8"/></g></svg>
          www.qelmotorgear.com
        </li>
      </ul>
    </div>
    <svg class="band" viewBox="0 0 690 12" preserveAspectRatio="none" aria-hidden="true">
      <rect width="690" height="12" fill="#444244"/>
      <polygon points="0,0 352,0 334,12 0,12" fill="#d91f26"/>
      <polygon points="352,0 358,0 340,12 334,12" fill="#ffffff"/>
    </svg>
  </section>

  <section class="card card--back" aria-label="Business card back">
    <div class="back-mark">
      <span class="back-mark__square"></span>
      <span class="back-mark__name">QEL MOTOR GEAR</span>
    </div>
  </section>
</body>
</html>
```